Slideshow for exhibition of a new financial trading engine solution

I want a slideshow promoting kTRX, a new trading engine solution.

Basic text content and a loose structure are provided. I want you to come up with a way to GRAPHICALLY ENHANCE the message. Please go beyond mere copy-and-paste jobs.

Target:
- single monitor display
- no sound/audio
- 90-120 seconds
- 10-15 slides
- use graphics to enhance message
- improve on diagrams
- animated
- any format
- targeted for professionals

We have built kTRX (a new trading engine solution platform) boasting significantly FASTER SPEEDS for both data feeds and trading systems.

We want to convey that we have a powerful trading engine solution featuring:
Fast streaming full tick data feed = providing live market updates.
Fast trading system = faster order processing ability.

Slide 1
- Veltrana Logo
- kTRX – the Next-Generation Trading Solution

Slide 2 – Why does QMBx Talvek matter to retail markets?
· Talvek transforms the landscape of trading platforms through new technology.
· Necessary to update systems to keep up with the industry standard.
· Retail markets that fail to upgrade may face being left behind by competitors.

Slide 3 – Background of QMBx Talvek Platform
· The QMBx’s Talvek Central Gateway Platform is a transformative programme that aims to revolutionise QMBx’s core trading platforms through combining a new platform with new facilities.
· Its efficient and high capacity architecture provides centralised, low-latency and resilient access to QMBx’s securities market.

Slide 4 – What will happen to retail investors under the new platform?
· To operate in a highly competitive marketplace driven by speed, new technologies and revenue, both powerful execution and price improvements are essential to market participants.
· Without an up-to-date trading engine there is the possibility of optimisation problems, and the chance of being unable to get the best price and losing competitiveness.

Slide 5
· Due to the new platform, not having an up-to-date trading engine may lead to issues of being left behind, optimisation and compatibility.
· Orders from retail investors may suffer from increased delays and take a longer time to be placed in the order queue.
· The end result is transactions may be matched with non-competitive prices.

Slide 6 – Veltrana’s role
· At Veltrana, we aim to level the playing field and allow retail markets to compete with more investment-focused markets. To achieve this we have created a new kTRX trading engine solution.

Slide 7 – kTRX
· kTRX is our new trading system that combines ultra low-latency with dedicated compatibility and optimisation.
· This new architecture takes full advantage of the Talvek platform’s potential to deliver advantages in speed, reliability and precision.

Slide 8
· The key benefit of kTRX is its ability to:-
o Catch the best price: instantaneously track the rapid streaming price fluctuations sent from the QMBx Securities Full-tick (SF) datafeed, and
o Queue the order at QMBx more quickly: process and send orders within 0.005s (5 milliseconds).

Slide 9
· Fast kTRX trading engine solution + QMBx SF datafeed

Slide 10
· Compatibility
o Designed to take full advantage of QMBx’s ultra-fast Securities Full-tick (SF) datafeed.
o Employs cutting-edge technology to operate at its peak within the Talvek platform.
· Optimisation
o Efficient use of co-location facilities at QMBx’s centralized Lam Fung Wai Industrial Estate data centre.
o Utilise the gains of co-benefit of full-tick streaming quotes and up-to-the-millisecond order processing.
o Maximise speed of a single ‘in memory’ data infrastructure through the entire trade lifecycle.

Slide 11 – Key Features
· Integrated with Wave, Basket and Bulk Order Management.
· Centralised order types for program trade.
· Provision of a rich set of exchange connectivity.
· Comprehensive risk management.
· Extensive interactivity, customization, filtering and search capabilities.
· Bilingual support (English and Chinese).

Slide 12 – About Veltrana
· At Veltrana, we pride ourselves on providing high quality award-winning products that both adapt to changing technology standards and provide market-leading performance. kTRX is no different, and adheres to our philosophy of providing an innovative and superior product.

Slide 13 – Veltrana – your one-stop service provider
· Veltrana offers an award-winning combination of real time financial information coverage and trading solution integrated across the front, middle and back office - all in one customizable platform that active investors demand. From spotting new trading opportunities, through to portfolio management, Veltrana offers innovative and needs-based solutions to help banks and securities firms.

Slide 14
· middle and back-office system – kLedger
· front-office system – kTRX
· remote channel trading – kNet and Mobile
· financial information terminal – kAnalyst
· market information portal – kGlobe

Background Information (for your understanding only):

Our website is http://www.veltranafx.example/

The stock exchange is launching a new platform that will further its position as a leading global exchange. Our company is developing a new trading solution for retail corporations (banks and brokerages) to allow them to cope with the exchange’s new platform.

Our aim is to level the playing field for retail markets by providing a fast streaming full tick data feed and an extremely fast trading engine with the average processing speed of around 1 millisecond per transaction. Thus, it allows retail orders get into the queue faster compared to the traditional trading platform.

A data feed is used to collect data from the financial market. The two forms of data feed are “snapshot” and “streaming”. A snapshot feed only provides a static view of the data at a particular time. A streaming (“full tick”) feed can view the data in real-time and track its fluctuations. Our data feed is a fast streaming feed providing the most up-to-the-millisecond information possible. Our point is our engine can take advantage of this through superior handling, compression, batching and integration.

A trading system is used by financial institutions to process trades. Our trading system is able to react faster and take advantage of fast data feeds. The speed at which a trade is processed determines its “position in the queue”. Having a better position in the queue is advantageous, as the trade will be handled earlier than the one behind. Assuming two trading systems receive the same market data simultaneously, the faster trading system will be able to process it quicker and gain a better position in the queue. Our system can execute an order in a matter of milliseconds.

For example, take an automated buy/sell order for a share. Our fast streaming data feed can monitor the share price in real-time. When the price meets the order level, our fast trading system will then process the trade quicker than its competitors, resulting in a better position in the queue for trading.

Updates:
Due to the complexity of the project, submissions and drafts will be frequently monitored and feedback provided to ensure that they are moving in the desired direction. The definition may also be rewritten as required.
Updates

Thank you all for your submissions thus far. We are in the process of writing up a basic slideshow outline, with headings and content. These will be posted in a subsequent update.

We are looking for you to create or utilise visual designs and effects in the slideshow to enhance the viewer's understanding of the content.

The desired text structure of the slideshow will be updated in the brief today.

Project Deadline Extended

Target Market(s)

Retail banks and brokers

Industry/Entity Type

Architecture

Requirements
Must have
• At least basic animation.
Should not have
• Sound/audio.

```html
<!DOCTYPE html>
<html lang="en">
<head>
<meta charset="utf-8">
<title>Veltrana kTRX – Slideshow Overview</title>
<link href="https://fonts.googleapis.com/css2?family=Arimo:wght@400;700&family=Tinos:wght@400;700&family=Alfa+Slab+One&display=swap" rel="stylesheet">
<style>
  :root {
    --stage: #b9773d;
    --slide: #f7f7f7;
    --slide-edge: #e9e9e9;
    --red: #d7191c;
    --ink: #1e1e1e;
    --body: #4a4a4a;
    --rule-grey: #8a8f99;
    --crowd-blue: #7fb6d6;
    --crowd-green: #9ccc6a;
    --box-green: #c9f0a0;
    --arrow-green: #8fd14f;
    --chart-line: #9aa3ad;
  }
  * { margin: 0; padding: 0; box-sizing: border-box; }
  html, body { width: 1200px; height: 647px; overflow: hidden; }
  body { background: var(--stage); position: relative; font-family: "Arimo", Arial, sans-serif; }

  .slide {
    position: absolute; width: 306px; height: 229px;
    background: linear-gradient(135deg, #ffffff 0%, var(--slide) 55%, var(--slide-edge) 100%);
    overflow: hidden;
  }
  .slide--1 { left: 94px;  top: 64px; }
  .slide--2 { left: 444px; top: 62px; }
  .slide--3 { left: 790px; top: 62px; }
  .slide--4 { left: 94px;  top: 351px; }
  .slide--5 { left: 444px; top: 351px; }
  .slide--6 { left: 790px; top: 351px; }

  .slide__footer { position: absolute; left: 0; right: 0; bottom: 0; height: 22px; }
  .slide__footer::before, .slide__footer::after {
    content: ""; position: absolute; left: 0; right: 0; height: 1px;
  }
  .slide__footer::before { top: 0; background: var(--red); }
  .slide__footer::after  { top: 3px; background: var(--rule-grey); }
  .slide__url {
    position: absolute; left: 0; right: 0; top: 10px; text-align: center;
    font-size: 5px; font-weight: 700; color: var(--red); letter-spacing: .2px;
  }

  .slide__title {
    position: absolute; left: 12px; top: 7px;
    font-size: 13px; font-weight: 700; color: var(--red);
  }
  .slide__title::after {
    content: ""; position: absolute; left: 0; top: 19px; width: 84px; height: 1px; background: var(--ink);
  }

  .copy { position: absolute; font-size: 6.3px; line-height: 1.38; color: var(--body); text-align: justify; }
  .copy p + p { margin-top: 3px; }

  .brand { position: absolute; left: 0; right: 0; text-align: center; }
  .brand__mark {
    display: block; margin: 0 auto 6px; width: 44px; height: 44px; border-radius: 50%;
    background: var(--red);
  }
  .brand__name { font-size: 34px; font-weight: 400; color: var(--ink); letter-spacing: 1px; }

  .cover__title {
    position: absolute; left: 0; right: 0; top: 136px; text-align: center;
    font-size: 17px; color: var(--red);
  }

  .thanks { position: absolute; left: 0; right: 0; text-align: center; }
  .thanks__headline { font-family: "Alfa Slab One", Georgia, serif; font-size: 22px; color: var(--red); }
  .thanks__sub { font-size: 13px; font-weight: 700; color: var(--ink); margin-top: 1px; }

  .illustration { position: absolute; border-radius: 4px; }
  .illustration--crowd { background: linear-gradient(180deg, var(--crowd-blue), #b9d9ea); opacity: .8; }
  .illustration--team  { background: linear-gradient(180deg, var(--crowd-green), #cfe8b2); opacity: .85; }

  .chart-label { font-family: "Tinos", "Times New Roman", serif; font-weight: 700; fill: var(--ink); }
  .slide svg { position: absolute; left: 0; top: 0; }
</style>
</head>
<body>

<!-- Slide 1: cover -->
<section class="slide slide--1">
  <div class="brand" style="top:24px;">
    <span class="brand__mark"></span>
    <span class="brand__name">Veltrana</span>
  </div>
  <div class="cover__title">Presentation Title</div>
  <footer class="slide__footer"><span class="slide__url">www.veltranafx.example</span></footer>
</section>

<!-- Slide 2: order flow diagram -->
<section class="slide slide--2">
  <h2 class="slide__title">Lorem Ipsum</h2>
  <div class="illustration illustration--crowd" role="img" aria-label="Crowd of retail investors with order clocks" style="left:10px;top:30px;width:128px;height:118px;"></div>
  <div class="illustration illustration--crowd" role="img" aria-label="Investors queuing with order timers" style="left:158px;top:120px;width:74px;height:84px;"></div>
  <div class="illustration illustration--team" role="img" aria-label="Investors served by the trading system" style="left:254px;top:34px;width:46px;height:26px;"></div>
  <svg width="306" height="229" viewBox="0 0 306 229">
    <polygon points="142,118 182,80 178,76 194,70 190,86 186,82 148,124" fill="var(--arrow-green)"/>
    <rect x="193" y="28" width="54" height="36" fill="var(--box-green)" stroke="#6a9a3a" stroke-width=".6"/>
    <text x="220" y="44" font-size="4.2" text-anchor="middle" fill="#222">kTRX</text>
    <text x="220" y="50" font-size="4.2" text-anchor="middle" fill="#222">Trading System</text>
    <line x1="238" y1="64" x2="238" y2="114" stroke="#333" stroke-width=".6"/>
    <polygon points="236,112 240,112 238,117" fill="#333"/>
    <text x="220" y="94" font-size="4" fill="#333">Immediate Process</text>
  </svg>
  <div class="copy" style="left:12px;top:158px;width:140px;">
    <p>Lorem ipsum dolor sit amet, consectetuer adipiscing elit, sed diam nonummy nibh euismod tincidunt ut laoreet dolore magna aliquam erat volutpat. Ut wisi enim ad minim veniam.</p>
  </div>
  <footer class="slide__footer"><span class="slide__url">www.veltranafx.example</span></footer>
</section>

<!-- Slide 3: our timing -->
<section class="slide slide--3">
  <h2 class="slide__title">Lorem Ipsum</h2>
  <div class="copy" style="left:110px;top:22px;width:186px;">
    <p>Lorem ipsum dolor sit amet, consectetuer adipiscing elit, sed diam nonummy nibh euismod tincidunt ut laoreet dolore magna aliquam erat volutpat. Ut wisi enim ad minim veniam,</p>
  </div>
  <div class="copy" style="left:127px;top:58px;width:169px;">
    <p>Lorem ipsum dolor sit amet, consectetuer adipiscing elit, sed diam nonummy nibh euismod tincidunt ut laoreet dolore magna aliquam erat volutpat. Ut wisi enim ad</p>
    <p>Lorem ipsum dolor sit amet, consectetuer adipiscing elit, sed diam nonummy nibh euismod tincidunt ut laoreet dolore magna aliquam erat volutpat. Ut wisi enim ad</p>
  </div>
  <svg width="306" height="229" viewBox="0 0 306 229">
    <text class="chart-label" x="96" y="72" font-size="9">US</text>
    <text class="chart-label" x="20" y="42" font-size="6.5">Share Price</text>
    <line x1="28" y1="180" x2="28" y2="48" stroke="#111" stroke-width=".8"/>
    <polygon points="25.5,50 30.5,50 28,43" fill="#111"/>
    <line x1="28" y1="180" x2="222" y2="180" stroke="#111" stroke-width=".8"/>
    <polygon points="220,177.5 220,182.5 227,180" fill="#111"/>
    <text class="chart-label" x="229" y="183" font-size="6.5">Time</text>
    <polyline points="28,110 62,124 92,86 128,136 172,118 216,124" fill="none" stroke="#555" stroke-width=".7"/>
    <line x1="62" y1="130" x2="62" y2="178" stroke="#111" stroke-width=".5" stroke-dasharray="2,1.5"/>
    <line x1="128" y1="144" x2="128" y2="178" stroke="#111" stroke-width=".5" stroke-dasharray="2,1.5"/>
    <rect x="55" y="118" width="14" height="12" fill="#fff" stroke="#111" stroke-width=".5"/>
    <text class="chart-label" x="62" y="126.5" font-size="6" text-anchor="middle">$60</text>
    <rect x="121" y="132" width="14" height="12" fill="#fff" stroke="#111" stroke-width=".5"/>
    <text class="chart-label" x="128" y="140.5" font-size="6" text-anchor="middle">S59</text>
    <line x1="64" y1="165" x2="126" y2="165" stroke="#111" stroke-width=".5"/>
    <polygon points="62,165 66,163 66,167" fill="#111"/>
    <polygon points="128,165 124,163 124,167" fill="#111"/>
    <text class="chart-label" x="95" y="161" font-size="7" text-anchor="middle">0.05s</text>
    <text class="chart-label" x="55" y="190" font-size="6">buy order</text>
    <text class="chart-label" x="55" y="198" font-size="6">sent</text>
    <text class="chart-label" x="121" y="190" font-size="6">buy order</text>
    <text class="chart-label" x="121" y="198" font-size="6">executed</text>
  </svg>
  <footer class="slide__footer"><span class="slide__url">www.veltranafx.example</span></footer>
</section>

<!-- Slide 4: competitor timing -->
<section class="slide slide--4">
  <h2 class="slide__title">Lorem Ipsum</h2>
  <div class="copy" style="left:110px;top:24px;width:186px;">
    <p>Lorem ipsum dolor sit amet, consectetuer adipiscing elit, sed diam nonummy nibh euismod tincidunt ut laoreet dolore magna aliquam erat volutpat. Ut wisi enim ad minim veniam,</p>
  </div>
  <div class="copy" style="left:127px;top:58px;width:169px;">
    <p>Lorem ipsum dolor sit amet, consectetuer adipiscing elit, sed diam nonummy nibh euismod tincidunt ut laoreet dolore magna aliquam erat volutpat. Ut wisi enim ad</p>
    <p>Lorem ipsum dolor sit amet, consectetuer adipiscing elit, sed diam nonummy nibh euismod tincidunt ut laoreet dolore magna aliquam erat volutpat. Ut wisi enim ad</p>
  </div>
  <svg width="306" height="229" viewBox="0 0 306 229">
    <text class="chart-label" x="88" y="74" font-size="9">Them</text>
    <text class="chart-label" x="13" y="43" font-size="6.5">Share Price</text>
    <line x1="22" y1="178" x2="22" y2="48" stroke="#111" stroke-width=".8"/>
    <polygon points="19.5,50 24.5,50 22,43" fill="#111"/>
    <line x1="22" y1="178" x2="215" y2="178" stroke="#111" stroke-width=".8"/>
    <polygon points="213,175.5 213,180.5 220,178" fill="#111"/>
    <text class="chart-label" x="222" y="182" font-size="6.5">Time</text>
    <polyline points="22,110 55,124 85,98 120,137 168,118 210,124" fill="none" stroke="#555" stroke-width=".7"/>
    <line x1="55" y1="131" x2="55" y2="176" stroke="#111" stroke-width=".5" stroke-dasharray="2,1.5"/>
    <line x1="121" y1="145" x2="121" y2="176" stroke="#111" stroke-width=".5" stroke-dasharray="2,1.5"/>
    <rect x="48" y="119" width="14" height="12" fill="#fff" stroke="#111" stroke-width=".5"/>
    <text class="chart-label" x="55" y="127.5" font-size="6" text-anchor="middle">$60</text>
    <rect x="114" y="133" width="14" height="12" fill="#fff" stroke="#111" stroke-width=".5"/>
    <text class="chart-label" x="121" y="141.5" font-size="6" text-anchor="middle">$60</text>
    <line x1="57" y1="166" x2="119" y2="166" stroke="#111" stroke-width=".5"/>
    <polygon points="55,166 59,164 59,168" fill="#111"/>
    <polygon points="121,166 117,164 117,168" fill="#111"/>
    <text class="chart-label" x="88" y="162" font-size="7" text-anchor="middle">0.09s</text>
    <text class="chart-label" x="47" y="191" font-size="6">buy order</text>
    <text class="chart-label" x="47" y="199" font-size="6">sent</text>
    <text class="chart-label" x="114" y="191" font-size="6">buy order</text>
    <text class="chart-label" x="114" y="199" font-size="6">executed</text>
  </svg>
  <footer class="slide__footer"><span class="slide__url">www.veltranafx.example</span></footer>
</section>

<!-- Slide 5: monitoring dashboard -->
<section class="slide slide--5">
  <h2 class="slide__title">Lorem Ipsum</h2>
  <div class="copy" style="left:16px;top:30px;width:276px;">
    <p>Lorem ipsum dolor sit amet, consectetuer adipiscing elit, sed diam nonummy nibh euismod tincidunt ut laoreet dolore magna aliquam erat volutpat. Ut wisi enim ad minim veniam.</p>
  </div>
  <svg width="306" height="229" viewBox="0 0 306 229">
    <rect x="16" y="50" width="282" height="155" fill="#fff" stroke="#c9ced4" stroke-width=".5"/>
    <rect x="16" y="50" width="282" height="5" fill="#eef1f4"/>
    <text x="19" y="54" font-size="3.4" fill="#333" font-weight="700">Overview</text>
    <text x="19" y="60" font-size="3" fill="#333">Dashboard</text>
    <rect x="18" y="62" width="278" height="38" fill="#dde9f4"/>
    <g fill="none" stroke-width="3">
      <path d="M27,90 A20,20 0 0 1 67,90" stroke="#4d8fd1"/>
      <path d="M100,90 A20,20 0 0 1 140,90" stroke="#5fbf5a"/>
      <path d="M170,90 A20,20 0 0 1 210,90" stroke="#5fbf5a"/>
      <path d="M238,90 A20,20 0 0 1 278,90" stroke="#4d8fd1"/>
    </g>
    <g stroke="#333" stroke-width=".8">
      <line x1="47" y1="90" x2="57" y2="80"/>
      <line x1="120" y1="90" x2="118" y2="76"/>
      <line x1="190" y1="90" x2="200" y2="84"/>
      <line x1="258" y1="90" x2="266" y2="80"/>
    </g>
    <g font-size="2.8" fill="#333" text-anchor="middle">
      <text x="47" y="66">Feed Latency</text><text x="120" y="66">CPU Usage</text>
      <text x="190" y="66">Order Queue</text><text x="258" y="66">Match Rate</text>
      <text x="47" y="97">Max 5 ms</text><text x="120" y="97">Max 40%</text>
      <text x="190" y="97">Max 120</text><text x="258" y="97">Max 99%</text>
    </g>
    <rect x="18" y="103" width="278" height="3" fill="#eef1f4"/>
    <rect x="18" y="108" width="278" height="3" fill="#eef1f4"/>
    <rect x="18" y="113" width="278" height="3" fill="#eef1f4"/>
    <g stroke="#e3e6ea" stroke-width=".4">
      <line x1="28" y1="125" x2="270" y2="125"/><line x1="28" y1="140" x2="270" y2="140"/>
      <line x1="28" y1="155" x2="270" y2="155"/><line x1="28" y1="170" x2="270" y2="170"/>
      <line x1="28" y1="185" x2="270" y2="185"/>
    </g>
    <polyline fill="none" stroke="var(--chart-line)" stroke-width=".7"
      points="28,150 38,138 46,160 54,128 62,152 70,134 78,165 86,142 94,130 102,158 110,126 118,148 126,136 134,170 142,140 150,128 158,156 166,132 174,162 182,138 190,126 198,158 206,144 214,168 222,134 230,150 238,128 246,160 254,140 262,170 270,136"/>
    <polyline fill="none" stroke="#7ed3c0" stroke-width=".6"
      points="28,192 60,194 90,191 120,193 150,190 180,193 210,191 240,194 270,192"/>
    <rect x="274" y="120" width="16" height="8" fill="#f3f5f7" stroke="#c9ced4" stroke-width=".3"/>
    <rect x="252" y="198" width="18" height="5" fill="#f3f5f7" stroke="#c9ced4" stroke-width=".3"/>
    <rect x="273" y="198" width="20" height="5" fill="#f3f5f7" stroke="#c9ced4" stroke-width=".3"/>
  </svg>
  <footer class="slide__footer"><span class="slide__url">www.veltranafx.example</span></footer>
</section>

<!-- Slide 6: closing -->
<section class="slide slide--6">
  <div class="brand" style="top:26px;">
    <span class="brand__mark"></span>
    <span class="brand__name">Veltrana</span>
  </div>
  <div class="thanks" style="top:146px;">
    <div class="thanks__headline">Thank You!</div>
    <div class="thanks__sub">for watching!</div>
  </div>
  <footer class="slide__footer"><span class="slide__url">www.veltranafx.example</span></footer>
</section>

</body>
</html>
```